verdant terraces simple classy business card design

my name is colin barrow and I run a gardening business aimed at high class verdant terraces. the business name is verdant terraces and our logo was designed on pixel harbour .My clientel are anything from residential homes to businesses. I take pride in my work and know that I offer a service like no other in my area.
The business card will be used to represent my business and I want it to be not only rememberable, but simplistic and modern. Eye catching too. Of course I would like it relatable to gardening and appealing to the correct clientel - those being garden enthusiasts, prestigious homes and businesses that are after top of the line gardening services like no other on the market.
I am not a typical lawn mowing business so I don't want a typical card design that represents that. The gardens I work with are generally million dollar properties with owners who are very garden proud looking for upkeep and guidance from me along with sometimes whole new garden designs. I want the business cards to show to my clients that I take pride, as they do, in their garden. And I want them to know from my card that I am a professional, qualified horticulturist offering them a top of the line service for life. I want them to refer my business on. I want them to look at my business card and see class and professionalism in a modern unique bold way.
The card should be simple with the possibility of the logo on the front being embossed/debossed and my details on the back the card should have a organic garden feel it's very important to me that it is absolutely perfect
I am also very open to ideas and suggestions so look forward to seeing the designs. the business logo has been supplied with this project and I want the card to be double sided

Contact info is
Colin Barrow - Managing Director / Horticulturist
Phone : 0481 526 704
Email: colinbarrow@verdantterraces.example.au

Target Market(s)

high class gardens residential and commercial

Industry/Entity Type

Gardener

Contact Information for Business Card

Contact info is
Phone : 0481 526 704

PLEASE MAKE CARD DOUBLE SIDED

Requirements
Must have
• organic simple classy modern feel
• must flow with the current logo that has been supplied with this project
• Double sided
• Must explain in a simple way that I deal with high end gardens and I'm a qualified horticulturist
Nice to have
• embossed debossed logo
Should not have
• shouldn't be to busy or cheap looking

```html
<!DOCTYPE html>
<html lang="en">
<head>
<meta charset="utf-8">
<title>Verdant Terraces – Business Card</title>
<link href="https://fonts.googleapis.com/css2?family=Montserrat:wght@400;600&display=swap" rel="stylesheet">
<style>
  :root {
    --backdrop: #2e2f31;
    --card-white: #ffffff;
    --leaf-green: #5c9e5c;
    --brand-green: #4f9a4f;
    --emboss-grey: #c9c9c9;
    --text-white: #ffffff;
  }
  * { margin: 0; padding: 0; box-sizing: border-box; }
  html, body {
    width: 1200px;
    height: 900px;
    overflow: hidden;
    background: var(--backdrop);
    font-family: "Montserrat", sans-serif;
  }
  .stage {
    position: relative;
    width: 1200px;
    height: 900px;
  }
  .card {
    position: absolute;
    width: 600px;
    height: 343px;
    left: 300px;
    border-radius: 22px;
    background: var(--card-white);
    overflow: hidden;
  }
  .card--front { top: 86px; }
  .card--back { top: 471px; }

  /* Front: debossed brand area */
  .front-mark {
    position: absolute;
    left: 50%;
    top: 50%;
    transform: translate(-50%, -50%);
    display: flex;
    align-items: center;
    gap: 14px;
  }
  .front-mark__dot {
    width: 18px;
    height: 18px;
    border-radius: 50%;
    background: var(--emboss-grey);
  }
  .front-mark__name {
    font-weight: 600;
    font-size: 30px;
    letter-spacing: 4px;
    text-transform: uppercase;
    color: var(--emboss-grey);
  }

  /* Back: details */
  .brand {
    position: absolute;
    right: 34px;
    top: 58px;
    display: flex;
    align-items: center;
    gap: 10px;
  }
  .brand__dot {
    width: 14px;
    height: 14px;
    border-radius: 50%;
    background: var(--brand-green);
  }
  .brand__name {
    font-weight: 600;
    font-size: 24px;
    letter-spacing: 3px;
    text-transform: uppercase;
    color: var(--brand-green);
  }
  .rule {
    position: absolute;
    left: 0;
    right: 0;
    top: 180px;
    height: 3px;
    background: var(--leaf-green);
  }
  .band {
    position: absolute;
    left: 0;
    right: 0;
    top: 190px;
    bottom: 0;
    background: var(--leaf-green);
    color: var(--text-white);
    padding: 22px 0 0 56px;
  }
  .band__name {
    font-weight: 600;
    font-size: 26px;
    line-height: 1.1;
  }
  .band__role {
    font-weight: 400;
    font-size: 15px;
    margin-top: 4px;
  }
  .contact {
    list-style: none;
    margin-top: 12px;
    font-size: 15px;
  }
  .contact li {
    display: flex;
    align-items: center;
    gap: 10px;
    line-height: 1.65;
  }
  .contact svg { width: 12px; height: 12px; fill: var(--text-white); flex: none; }
</style>
</head>
<body>
<main class="stage">
  <section class="card card--front" aria-label="Card front">
    <div class="front-mark">
      <span class="front-mark__dot"></span>
      <span class="front-mark__name">verdant terraces</span>
    </div>
  </section>

  <section class="card card--back" aria-label="Card back">
    <div class="brand">
      <span class="brand__dot"></span>
      <span class="brand__name">verdant terraces</span>
    </div>
    <div class="rule"></div>
    <div class="band">
      <h1 class="band__name">Colin Barrow</h1>
      <p class="band__role">Managing Director / Horticulturist</p>
      <ul class="contact">
        <li>
          <svg viewBox="0 0 24 24" aria-hidden="true"><path d="M6.6 10.8a15 15 0 0 0 6.6 6.6l2.2-2.2c.3-.3.7-.4 1-.2 1.1.4 2.3.6 3.6.6.6 0 1 .4 1 1V20c0 .6-.4 1-1 1C10.6 21 3 13.4 3 4c0-.6.4-1 1-1h3.5c.6 0 1 .4 1 1 0 1.3.2 2.5.6 3.6.1.3 0 .7-.2 1z"/></svg>
          <span>0481 526 704</span>
        </li>
        <li>
          <svg viewBox="0 0 24 24" aria-hidden="true"><path d="M2 5h20v14H2zM4 7v.5l8 5 8-5V7l-8 5z"/></svg>
          <span>colinbarrow@verdantterraces.example.au</span>
        </li>
      </ul>
    </div>
  </section>
</main>
</body>
</html>
```